Creation of an elegant and modern turnkey Shopify website

Hello,

We are a new company specializing in the sale of above-ground pools. We want to create a turnkey website, ideally using Shopify. For now, we need a "showcase" site, not an e-commerce platform, with four tabs:

Home Page (an overall presentation of the company)
Our Products (an overview of all the above-ground pools we sell)
Our Projects (a page inspired by Instagram to showcase photos of our future projects)
Contact (a page with all our contact information and a contact form)

We are looking to create a highly visual, elegant, and modern website with vibrant splashes of color. We will provide the text, photos (along with instructions on where to place them on each page), and all other necessary information as attachments.

Thank you in advance for your proposals!

The Brisa Lagoon Team

Target Market(s)

Targeted at Swiss customers (a translator will need to be installed for different languages)

Industry/Entity Type

Sale of customised above-ground pools

Coding

Coded - Design and coding required

Font styles to use
Sans Serif

Colors
0094D4
00A9DD
6FCCEA
C7EBF8
E9F6FB
00AB8E
00BBA5
67D7C9
C6EFE9
E9F9F6

Requirements
Must have
• A stunning, elegant and modern look
Nice to have
• Inspiration from the colors of our logo throughout the site, but in an elegant way
Should not have
• An overly classic look for swimming pool sites

```html
<!DOCTYPE html>
<html lang="en">
<head>
<meta charset="utf-8">
<title>Brisa Lagoon – Premium Above-Ground Pools</title>
<link href="https://fonts.googleapis.com/css2?family=Josefin+Sans:wght@300;700&family=Lato:wght@400;700&family=Catamaran:wght@400;500&display=swap" rel="stylesheet">
<style>
:root{
  --blue-deep:#0094D4;
  --blue:#00A9DD;
  --blue-soft:#6FCCEA;
  --blue-pale:#C7EBF8;
  --blue-mist:#E9F6FB;
  --teal-deep:#00AB8E;
  --teal:#00BBA5;
  --ink:#111111;
  --text:#333333;
  --footer:#2b2b2b;
  --white:#ffffff;
}
*{margin:0;padding:0;box-sizing:border-box}
html,body{width:1200px;height:3338px;overflow:hidden;background:var(--white)}
body{position:relative;font-family:"Lato",sans-serif;color:var(--text)}
.abs{position:absolute}
.logo{font-family:"Josefin Sans",sans-serif;font-weight:300;color:var(--blue);text-transform:uppercase;line-height:1.05;letter-spacing:1px;white-space:nowrap}
.site-logo{left:75px;top:34px;font-size:26px}
.footer-logo{left:615px;top:70px;font-size:30px}
.nav{top:58px;left:660px;display:flex;gap:42px;font-size:14px;letter-spacing:.5px;color:var(--ink)}
.nav a{color:inherit;text-decoration:none}
.nav .active{color:var(--blue-deep);border-bottom:2px solid var(--blue-deep);padding-bottom:3px}
.hero-title{left:75px;top:152px;width:520px;font-family:"Josefin Sans",sans-serif;font-weight:700;font-size:48px;line-height:51px;color:var(--ink);text-transform:uppercase;white-space:nowrap}
.hero-sub{left:75px;top:414px;width:440px;font-weight:700;font-size:22px;line-height:30px;color:var(--blue-deep)}
.hero-text{left:75px;top:484px;width:515px;font-size:14px;line-height:25.6px}
.btn{left:75px;top:640px;width:151px;height:46px;background:var(--teal);color:var(--white);font-size:15px;display:flex;align-items:center;justify-content:center;letter-spacing:.5px}
.photo{display:block}
.arrow{width:20px;height:28px}
.section-title{font-family:"Catamaran",sans-serif;font-weight:500;font-size:42px;line-height:40px;color:var(--ink)}
.acc{left:615px;width:511px;background:var(--blue-mist);padding:0 23px}
.acc-title{font-family:"Catamaran",sans-serif;font-size:21px;color:var(--ink);display:flex;justify-content:space-between;align-items:center}
.acc-open .acc-title{color:var(--blue-deep)}
.acc-body{font-size:15px;line-height:24px;color:var(--text);margin-top:8px}
.body-copy{font-size:14px;line-height:27px}
.sat-box{left:75px;top:2089px;width:328px;height:360px;background:var(--blue);padding:28px 24px;color:var(--white)}
.sat-box .section-title{color:var(--white)}
.contact-band{left:0;top:2536px;width:1200px;height:375px;background:linear-gradient(160deg,#0aa8dc 0%,#0094D4 45%,#1ab0e2 70%,#0782bd 100%);text-align:center;color:var(--white)}
.contact-band h2{font-family:"Catamaran",sans-serif;font-weight:400;font-size:43px;margin-top:102px}
.contact-band p{font-size:20px;line-height:33px;margin:14px auto 0;width:880px}
.footer{left:0;top:2911px;width:1200px;height:427px;background:var(--footer);color:var(--white)}
.footer h4{font-weight:400;font-size:19px;letter-spacing:.5px}
.footer ul{list-style:none;margin-top:12px}
.footer li{font-size:13px;line-height:37px}
.tagline{left:770px;top:100px;font-family:"Catamaran",sans-serif;font-size:21px;white-space:nowrap}
.social span,.cards span{display:inline-block}
.social span{width:18px;height:18px;border-radius:50%;background:var(--white);margin-right:20px}
.cards span{width:36px;height:22px;border-radius:3px;background:var(--white);margin:0 6px}
</style>
</head>
<body>

<header>
  <div class="abs logo site-logo">Brisa<br>Lagoon</div>
  <nav class="abs nav">
    <a class="active">HOME</a><a>OUR PRODUCTS</a><a>OUR WORKS</a><a>CONTACT US</a>
  </nav>
</header>

<section class="hero">
  <h1 class="abs hero-title">Transform your<br>garden with our<br>premium<br>above-ground<br>pools!</h1>
  <p class="abs hero-sub">Achieve your dreams with our custom, tailor-made above-ground pools.</p>
  <p class="abs hero-text">Imagine an exceptional relaxation and leisure space right in your own backyard. With our unparalleled expertise and commitment to excellence, we create above-ground pools that exceed all expectations. Our exclusive, custom-designed models are crafted to combine style, durability, and innovation, offering a unique and refined experience.</p>
  <div class="abs btn">READ MORE</div>
  <svg class="abs arrow" style="left:584px;top:375px" viewBox="0 0 20 28"><path d="M14 4 L5 14 L14 24" fill="none" stroke="#111" stroke-width="2"/></svg>
  <div class="abs photo" style="left:615px;top:144px;width:511px;height:556px;background:linear-gradient(180deg,#e4e6e8 0%,#c9ccce 35%,#6f7a72 52%,#4ba3bd 70%,#6e7f52 85%,#6c5a44 100%)" role="img" aria-label="Modern villa with a long rectangular pool in a green lawn"></div>
  <svg class="abs arrow" style="left:1138px;top:375px" viewBox="0 0 20 28"><path d="M6 4 L15 14 L6 24" fill="none" stroke="#111" stroke-width="2"/></svg>
</section>

<section class="why">
  <h2 class="abs section-title" style="left:75px;top:806px">Why Choose Our<br>Above-Ground Pools?</h2>
  <div class="abs photo" style="left:75px;top:915px;width:512px;height:531px;background:linear-gradient(135deg,#b8aaa0 0%,#a39389 40%,#3c6cc0 65%,#2a55b0 100%)" role="img" aria-label="Two workers laying blue mosaic tiles inside a pool"></div>

  <div class="abs acc acc-open" style="top:915px;height:118px;padding-top:18px">
    <div class="acc-title">Superior Quality
      <svg width="12" height="8" viewBox="0 0 12 8"><path d="M1 1 L6 6 L11 1" fill="none" stroke="#0094D4" stroke-width="2.2"/></svg></div>
    <p class="acc-body">Each pool is constructed with high-quality materials, ensuring exceptional durability and strength.</p>
  </div>
  <div class="abs acc" style="top:1052px;height:61px"><div class="acc-title" style="height:61px">Elegant Design
    <svg width="8" height="12" viewBox="0 0 8 12"><path d="M1 1 L6 6 L1 11" fill="none" stroke="#0094D4" stroke-width="2.2"/></svg></div></div>
  <div class="abs acc" style="top:1135px;height:61px"><div class="acc-title" style="height:61px">Custom and Tailor-Made
    <svg width="8" height="12" viewBox="0 0 8 12"><path d="M1 1 L6 6 L1 11" fill="none" stroke="#0094D4" stroke-width="2.2"/></svg></div></div>
  <div class="abs acc" style="top:1216px;height:62px"><div class="acc-title" style="height:62px">Easy Installation
    <svg width="8" height="12" viewBox="0 0 8 12"><path d="M1 1 L6 6 L1 11" fill="none" stroke="#0094D4" stroke-width="2.2"/></svg></div></div>
</section>

<section class="services">
  <div class="abs photo" style="left:75px;top:1546px;width:344px;height:450px;background:linear-gradient(160deg,#5cc4ea 0%,#2d8fd6 55%,#b9a89a 100%)" role="img" aria-label="Technician rolling a blue solar cover onto a pool"></div>
  <div class="abs photo" style="left:419px;top:1546px;width:347px;height:450px;background:linear-gradient(180deg,#6f9ccd 0%,#4d6a3e 40%,#123a4e 70%,#8a5e3b 100%)" role="img" aria-label="Dark pool edged with wooden decking and garden trees"></div>
  <h2 class="abs section-title" style="left:793px;top:1642px">Personalized<br>Services</h2>
  <p class="abs body-copy" style="left:793px;top:1736px;width:335px">We understand that every garden and client is unique. That's why we offer personalized services, from design to installation and after-sales support. Our team of experts is here to answer all your questions and guide you throughout your project.</p>
</section>

<section class="satisfaction">
  <div class="abs sat-box">
    <h2 class="section-title">Guaranteed<br>Satisfaction</h2>
    <p class="body-copy" style="margin-top:18px">Your satisfaction is our top priority.<br>We are committed to providing you with exceptional service and the highest quality products. Join our community of satisfied customers who are already enjoying their custom above-ground pools.</p>
    <p style="font-weight:700;font-size:16px;margin-top:12px">10-Year Warranty!</p>
  </div>
  <div class="abs photo" style="left:437px;top:2089px;width:329px;height:360px;background:linear-gradient(180deg,#eef0ee 0%,#8fb0a0 30%,#6cc3d8 60%,#2f3336 100%)" role="img" aria-label="Round above-ground pool on a white terrace with plants"></div>
  <div class="abs photo" style="left:798px;top:2089px;width:329px;height:360px;background:linear-gradient(160deg,#e8e8e6 0%,#8cc6d6 45%,#3d7a3c 75%,#2e3032 100%)" role="img" aria-label="Round above-ground pool beside a white balustrade and palm"></div>
</section>

<section class="abs contact-band" role="img" aria-label="Splashing blue water background">
  <h2>Contact Us Today</h2>
  <p>Don’t wait any longer to transform your garden into a wellness oasis. Contact us today to discover our range of customizable above-ground pools and get a tailored quote.<br>Dive into a world of infinite possibilities with Brisa Lagoon.</p>
</section>

<footer class="abs footer">
  <div class="abs" style="left:75px;top:70px">
    <h4>QUICK LINKS</h4>
    <ul><li>Home</li><li>Our Products</li><li>Our Works</li><li>Contact Us</li></ul>
  </div>
  <div class="abs logo footer-logo">Brisa<br>Lagoon</div>
  <p class="abs tagline">We Bring Your Pool Dreams to Life!</p>
  <div class="abs social" style="left:615px;top:210px" aria-label="Social media links"><span></span><span></span><span></span><span></span><span></span></div>
  <div class="abs" style="left:75px;top:289px;width:1050px;height:1px;background:#555"></div>
  <div class="abs cards" style="left:0;width:1200px;top:331px;text-align:center" aria-label="Accepted payment methods"><span></span><span></span><span></span><span></span><span></span><span></span></div>
  <p class="abs" style="left:0;width:1200px;top:376px;text-align:center;font-size:12px;color:#ddd">Copyright © 2024. Brisa Lagoon Sàrl All Right Reserved</p>
</footer>

</body>
</html>
```